Pay-Per-Use Production Space Warehouse/Factory/Production Space

Please refer to project requirements as attached/included. This is an introductory marketing Info graphic to capture attention or create awareness to a new, epic and unique business value preposition and business model for customer to easily launch new products/services and robust supply chain. This is a win win revolutionary business solution compare with traditional or conventional methods of outsourcing or DIY design, build, finance, operate and maintain. PROJECT Requirement to info graphic designer
1) Subject to confidentiality and all rights reserved
2) Below are some photos which you may consider to use for this work
3) Clarify and verify with us if there are any questions related to this work and design

Target Market(s)

Global, (Life sciences, food, others)

Industry/Entity Type

Medical And Science

Requirements
Must have
• Dynamic background template.
Should not have
• Monotonous and un-creative designs

```html
<!DOCTYPE html>
<html lang="en">
<head>
<meta charset="utf-8">
<title>Pay-Per-Use Production Space</title>
<link rel="stylesheet" href="https://fonts.googleapis.com/css2?family=Oswald:wght@500;600;700&family=Open+Sans:wght@400;600&display=swap">
<style>
  :root {
    --canvas: #ffffff;
    --sky-top: #4a4766;
    --sky-mid: #7b7b8f;
    --building: #a9a9a4;
    --ground: #3b3a3c;
    --panel: rgba(200, 88, 44, 0.93);
    --white: #ffffff;
    --ink: #333333;
    --muted: #777777;
    --badge-navy: #1f2a5c;
    --badge-green: #3d8f3a;
    --badge-purple: #7a2d8f;
    --badge-orange: #e0661f;
    --icon-purple: #5b3d8e;
    --icon-green: #2f8a4f;
    --icon-red: #c8332b;
  }
  html, body { margin: 0; padding: 0; overflow: hidden; }
  body { width: 849px; height: 1200px; background: var(--canvas); position: relative; font-family: "Open Sans", Arial, sans-serif; }
  .hero-photo {
    position: absolute; left: 0; top: 0; width: 849px; height: 850px;
    background: linear-gradient(180deg, var(--sky-top) 0%, var(--sky-mid) 24%, var(--building) 42%, #8d8c88 62%, var(--ground) 82%, #2c2b2d 100%);
  }
  .offer-panel { position: absolute; left: 76px; top: 400px; width: 392px; height: 515px; }
  .panel-shape { position: absolute; left: 0; top: 0; }
  .offer-content { position: absolute; left: 0; top: 0; width: 392px; text-align: center; color: var(--white); font-family: "Oswald", "Arial Narrow", sans-serif; }
  .offer-title { margin: 36px 0 0; font-size: 36px; line-height: 40px; font-weight: 700; letter-spacing: 0.5px; }
  .audience-icons { display: flex; justify-content: center; gap: 18px; margin-top: 30px; }
  .audience-icon { width: 72px; height: 72px; border-radius: 50%; border: 4px solid var(--white); box-sizing: border-box; display: flex; align-items: center; justify-content: center; }
  .audience-icon.purple { background: var(--icon-purple); }
  .audience-icon.green { background: var(--icon-green); }
  .audience-icon.red { background: var(--icon-red); }
  .audience-list { margin: 22px 0 0; font-size: 29px; line-height: 36px; font-weight: 600; }
  .value-block { position: absolute; left: 305px; top: 918px; width: 530px; color: var(--ink); font-size: 12px; line-height: 16px; }
  .value-block p { margin: 0 0 6px; white-space: nowrap; }
  .benefit-row { position: absolute; left: 283px; top: 1052px; display: flex; align-items: flex-start; }
  .benefit { width: 88px; text-align: center; font-family: "Oswald", sans-serif; font-size: 12px; font-weight: 600; color: var(--ink); letter-spacing: 0.5px; }
  .benefit-badge { width: 52px; height: 52px; border-radius: 50%; margin: 0 auto 8px; display: flex; align-items: center; justify-content: center; border: 3px solid #d9d9d9; box-sizing: border-box; }
  .divider { width: 1px; height: 22px; background: var(--badge-orange); margin: 56px 12px 0; }
  .footnote { position: absolute; left: 305px; top: 1138px; margin: 0; font-size: 9px; color: var(--muted); }
</style>
</head>
<body>
  <div class="hero-photo" role="img" aria-label="Architectural render of a modern production facility with glass entrance at dusk, a car in the foreground"></div>

  <section class="offer-panel">
    <svg class="panel-shape" width="392" height="515" viewBox="0 0 392 515">
      <polygon points="0,0 392,0 392,440 240,440 196,510 152,440 0,440" fill="var(--panel)"/>
    </svg>
    <div class="offer-content">
      <h1 class="offer-title">PAY-PER-USE<br>APPLICABLE TO ALL</h1>
      <div class="audience-icons">
        <div class="audience-icon purple">
          <svg width="38" height="26" viewBox="0 0 38 26"><rect x="2" y="8" width="34" height="16" fill="none" stroke="#fff" stroke-width="2.5"/><path d="M8 8V3h22v5" fill="none" stroke="#fff" stroke-width="2.5"/></svg>
        </div>
        <div class="audience-icon green">
          <svg width="38" height="30" viewBox="0 0 38 30"><path d="M3 28V12l8-5v5l8-5v5l8-5v21z" fill="none" stroke="#fff" stroke-width="2.5"/><rect x="29" y="2" width="5" height="26" fill="none" stroke="#fff" stroke-width="2.5"/></svg>
        </div>
        <div class="audience-icon red">
          <svg width="30" height="34" viewBox="0 0 30 34"><rect x="3" y="2" width="24" height="30" fill="none" stroke="#fff" stroke-width="2.5"/><path d="M9 9h4M17 9h4M9 16h4M17 16h4M12 32v-8h6v8" stroke="#fff" stroke-width="2.5" fill="none"/></svg>
        </div>
      </div>
      <p class="audience-list">START UPS/SMALL<br>MEDIUM ENTERPRISES/<br>MULTINATIONAL<br>CORPORATIONS/OTHERS</p>
    </div>
  </section>

  <section class="value-block">
    <p>Value Propositions(*):</p>
    <p>Maximum Technical and Financial Flexibility to Scale Up or Down with Ease.<br>This will allow you to Mitigate Risks, Change Swiftly and to Engage Success Better</p>
    <p>If Apply &amp; Use Continuously, It Gives Your Organization NEW STRATEGIC OPTION<br>to Gain the Competitive Advantage to Launch New Products/Services and<br>or Robust Supply Chain</p>
  </section>

  <div class="benefit-row">
    <div class="benefit">
      <div class="benefit-badge" style="background:var(--badge-navy)"><svg width="22" height="22" viewBox="0 0 22 22"><text x="11" y="17" text-anchor="middle" fill="#fff" font-family="Oswald, sans-serif" font-size="18" font-weight="700">$</text></svg></div>
      CHEAPER
    </div>
    <div class="divider"></div>
    <div class="benefit">
      <div class="benefit-badge" style="background:var(--badge-green)"><svg width="22" height="22" viewBox="0 0 22 22"><path d="M11 2l2.6 6 6.4.5-4.9 4.2 1.5 6.3L11 15.6 5.4 19l1.5-6.3L2 8.5 8.4 8z" fill="#fff"/></svg></div>
      BETTER
    </div>
    <div class="divider"></div>
    <div class="benefit">
      <div class="benefit-badge" style="background:var(--badge-purple)"><svg width="22" height="22" viewBox="0 0 22 22"><path d="M3 11h13M11 5l6 6-6 6" stroke="#fff" stroke-width="3" fill="none"/></svg></div>
      FASTER
    </div>
    <div class="divider"></div>
    <div class="benefit">
      <div class="benefit-badge" style="background:var(--badge-orange)"><svg width="22" height="22" viewBox="0 0 22 22"><path d="M3 11l5 5 11-11" stroke="#fff" stroke-width="3" fill="none"/></svg></div>
      ASSURED
    </div>
  </div>

  <p class="footnote">**Contact us for more information</p>
</body>
</html>
```